Property Services Company Needs a Brochure Design

Looking for a new brochure design for an existing property services company.

We provide a range of property services from, market research, real estate brokerage, valuation and appraisal, property development and other real estate consulting services.

We would like a fresh modern brochure design with good graphics and features. Our colours are white, blue and orange.

The design should communicate, attention to detail, superior service delivery and distinction in results.
Updates

I would like the brochure to be roughly about 20 pages.

Containing the following,

1) An introduction
2) Contents Page
2) What we do
3) Our Services
4) Agency & Brokerage
5) Real Estate Consulting
6) Market Research
7) Appraisal & Valuation
8) Project Management
9) Property Development

I would also like icons to represent items 4,5,6,7,8 & 9, they should be represented vertically on each of the pages from the contents page and highlighted individually on the pages that they represent.. i.e. on appraisal & valuation page, all six icons will be arranged vertically and the appraisal and valuations icon will be highlighted.

I will also like to have images that depict the services on the various pages.

I have some pages I think will flow which I will upload shortly.

Industry/Entity Type

Real Estate

Font styles to use
Serif

Colors
f78f20
0455a3

```html
<!DOCTYPE html>
<html lang="en">
<head>
<meta charset="utf-8">
<title>Halvern Property Services – Brochure Cover</title>
<link href="https://fonts.googleapis.com/css2?family=Questrial&display=swap" rel="stylesheet">
<style>
  :root {
    --backdrop: #e4e4e4;
    --paper: #ffffff;
    --brand-orange: #e07b3e;
    --brand-orange-deep: #d46a2e;
    --brand-purple: #4e4477;
    --brand-purple-light: #5e5488;
    --ink: #4a4a4a;
    --ink-soft: #6a6a6a;
  }
  * { margin: 0; padding: 0; box-sizing: border-box; }
  html, body {
    width: 1200px;
    height: 720px;
    overflow: hidden;
    background: var(--backdrop);
    font-family: "Questrial", sans-serif;
  }
  .canvas {
    position: relative;
    width: 1200px;
    height: 720px;
  }
  .brochure-cover {
    position: absolute;
    left: 380px;
    top: 50px;
    width: 440px;
    height: 620px;
    background: var(--paper);
    box-shadow: 0 6px 18px rgba(0, 0, 0, 0.18);
    overflow: hidden;
  }
  .cover-header {
    position: absolute;
    left: 0; top: 0;
    width: 100%;
    height: 80px;
  }
  .brand-lockup {
    position: absolute;
    right: 32px;
    top: 24px;
    display: flex;
    align-items: center;
    gap: 8px;
  }
  .brand-mark {
    width: 22px;
    height: 22px;
    background: var(--brand-orange);
  }
  .brand-text {
    display: flex;
    flex-direction: column;
    line-height: 1;
    color: var(--ink);
  }
  .brand-name {
    font-size: 26px;
    letter-spacing: 0.5px;
  }
  .brand-tagline {
    font-size: 9px;
    margin-top: 3px;
    color: var(--ink-soft);
    letter-spacing: 0.3px;
  }
  .header-rule {
    position: absolute;
    left: 0; top: 80px;
    width: 100%;
    height: 12px;
    background: var(--brand-purple);
  }
  .cover-art {
    position: absolute;
    left: 0; top: 0;
    width: 440px;
    height: 620px;
  }
  .cover-emboss {
    position: absolute;
    left: 0;
    top: 190px;
    width: 100%;
    text-align: center;
    font-size: 40px;
    color: var(--brand-orange-deep);
    letter-spacing: 1px;
  }
</style>
</head>
<body>
  <main class="canvas">
    <article class="brochure-cover">
      <svg class="cover-art" viewBox="0 0 440 620" aria-hidden="true">
        <defs>
          <linearGradient id="orangeSheen" x1="0" y1="0" x2="1" y2="0">
            <stop offset="0" stop-color="#d8702f"/>
            <stop offset="0.45" stop-color="#e9915c"/>
            <stop offset="1" stop-color="#e07b3e"/>
          </linearGradient>
          <linearGradient id="purpleSheen" x1="0" y1="0" x2="1" y2="0">
            <stop offset="0" stop-color="#4a4073"/>
            <stop offset="0.45" stop-color="#6a6092"/>
            <stop offset="1" stop-color="#4e4477"/>
          </linearGradient>
        </defs>
        <path class="band-orange" d="M0 112 H440 V400 Q220 440 0 430 Z" fill="url(#orangeSheen)"/>
        <path class="band-purple" d="M0 452 Q220 462 440 420 V592 H0 Z" fill="url(#purpleSheen)"/>
      </svg>

      <header class="cover-header">
        <div class="brand-lockup">
          <span class="brand-mark"></span>
          <div class="brand-text">
            <span class="brand-name">Halvern</span>
            <span class="brand-tagline">Property Services</span>
          </div>
        </div>
      </header>
      <div class="header-rule"></div>

      <div class="cover-emboss">Halvern</div>
    </article>
  </main>
</body>
</html>
```